Verpackungsdesign für Pasta aus Buchweizen
Zielgruppe
Unser Unternehmen VELMORIA sucht ein sehr modernes Verpackungsdesign für Pasta aus Buchweizen.
Unsere Produkte sind in unserem Online Shop und unterscheiden sich durch die herkömmliche Pasta, da wir Buchweizen in die Verarbeitung mit aufnehmen und somit die gesundheitsfördernde Eigenschaft des Buchweizens im Vordergrund steht. Unsere Pasta aus Buchweizenmehl mit klassischem Hartweizengrieß ist in dieser Form noch nicht im stationären Handel erhältlich, deshalb wünschen wir uns ein neues, ansprechendes Verpackungsdesign welches von den Massenprodukten aus den Regalen im Handel heraussticht. Das Design sollte also minimalistisch und sehr modern wirken, und sich deutlich von der Konkurrenz abheben.
Die Zielgruppe richtet sich sowohl an Massen die Pasta in allen Variationen lieben, als auch an ernährungsbewusste Veganer/Vegetarier die Alternativen im Bereich der herkömmlichen Pasta Kochkultur suchen.
PS: Mit dem Verkauf unserer Pasta investieren wir außerdem in den Aufbau und der Infrastruktur des Erzeugerlandes. Durch unser Prinzip „Teilen & Wachsen“ fördern wir mit unseren Gewinnen nachhaltige Projekte in den Erzeugerländern und helfen somit wirtschaftlich benachteiligten Regionen auf der Welt. (Fair Trade)
Aufgabenstellung
Wir besitzen bereits ein Logo und Verpackungen für unsere Pasta Sorten. Das Logo und das Grundgerüst der Stanzform / Verpackungsmaße (inkl. Sichtfenster) soll beibehalten werden (Siehe Anhang). Als Pasta Verpackungen benutzen wir Faltschachteln und Banderolen.
Verpackungsmaße:
- Faltschachtel (90 x 40 x 165 mm)
- Banderole (560 x 70mm)
Der Produktname ist je nach Sorte zu präzisieren:
- Fusilli
- Makkaroni
- Bandnudeln
- Tarhana
Produktgewicht:
- 250g
Eigenschaften:
- Buchweizenmehl
- 100% Vegan
- Kochzeit 3 Minuten
- Liebevolle Handarbeit
WICHTIG:
1) Bitte benutzt die hochgeladene, leere Stanzform für Artwork.
2) Die Designfarbe kann anhand des Aufstellers ausgerichtet werden (CMYK: 0, 20, 32, 0 und 60, 57, 56, 62) es ist aber kein muss und ihr seit frei in der Kreativität.
3) Bitte das Sichtfenster mit Rand wie aktuell auf den Produkten übernehmen (siehe www.velmoria.de/shop)
Nach dem Wettbewerb planen wir zusätzlich ein 1zu1 Projekt und würden uns freuen einen Gewinner auszuwählen - Wir freuen uns auf eure Ideen :)

```html
<!DOCTYPE html>
<html lang="de">
<head>
<meta charset="utf-8">
<title>VELMORIA Buchweizen Pasta – Faltschachtel</title>
<link rel="stylesheet" href="https://fonts.googleapis.com/css2?family=Bodoni+Moda:wght@400;500&family=Open+Sans:wght@300;400&family=Herr+Von+Muellerhoff&display=swap">
<style>
  :root {
    --stage: #d9d9d9;
    --paper: #ffffff;
    --ink: #111111;
    --brand-brown: #6b4a40;
    --band: #9b716a;
    --band-text: #f6ece8;
    --pasta-dark: #8a5a36;
    --pasta-light: #d9b49a;
    --icon-tone: #e6e6e6;
    --vegan-green: #6a9a3c;
    --body-text: #2a2a2a;
  }
  * { margin: 0; padding: 0; box-sizing: border-box; }
  html, body { width: 1200px; height: 1148px; overflow: hidden; }
  body { background: var(--stage); position: relative; font-family: "Open Sans", Arial, sans-serif; }

  .dieline { position: absolute; left: 245px; top: 124px; display: flex; box-shadow: 0 10px 30px rgba(0,0,0,.12); }
  .panel { position: relative; height: 900px; background: var(--paper); overflow: hidden; }
  .panel--side { width: 218px; border-right: 1px solid #ececec; }
  .panel--front { width: 491px; }

  /* side panel */
  .cook-time { position: absolute; top: 240px; width: 100%; text-align: center; font-weight: 300; font-size: 19px; line-height: 26px; color: var(--ink); letter-spacing: .5px; }
  .cook-icon { position: absolute; top: 318px; left: 69px; width: 80px; height: 84px; border-radius: 10px; background: var(--icon-tone); }
  .side-band { position: absolute; left: 0; top: 495px; width: 100%; height: 75px; background: var(--band); }
  .side-copy { position: absolute; left: 22px; width: 174px; font-size: 8px; line-height: 10.5px; text-align: justify; color: var(--body-text); }
  .side-copy--intro { top: 472px; }
  .side-copy--info { top: 576px; }
  .side-copy--prep { top: 622px; }
  .vegan-badge { position: absolute; left: 82px; top: 770px; width: 52px; height: 52px; border-radius: 50%; background: var(--vegan-green); border: 3px solid #fff; box-shadow: 0 0 0 1.5px var(--vegan-green); }
  .net-weight { position: absolute; top: 852px; width: 100%; text-align: center; font-weight: 300; font-size: 15px; color: var(--ink); }

  /* front panel */
  .brand { position: absolute; top: 78px; width: 100%; display: flex; justify-content: center; align-items: center; gap: 10px; }
  .brand__mark { width: 14px; height: 14px; border-radius: 50%; background: var(--brand-brown); }
  .brand__name { font-family: "Bodoni Moda", Georgia, serif; font-weight: 500; font-size: 30px; letter-spacing: 1px; color: var(--brand-brown); }

  .product-title { position: absolute; top: 250px; left: 88px; font-family: "Bodoni Moda", Georgia, serif; color: var(--ink); font-weight: 400; }
  .product-title__sub { display: block; font-size: 42px; letter-spacing: 3px; line-height: 46px; }
  .product-title__main { display: block; font-size: 94px; letter-spacing: 4px; line-height: 92px; margin-left: -2px; }
  .product-title__script { position: absolute; top: 370px; left: 262px; font-family: "Herr Von Muellerhoff", cursive; font-size: 56px; color: var(--ink); transform: rotate(-6deg); }

  .variety-band { position: absolute; left: 0; top: 495px; width: 243px; height: 75px; background: var(--band); display: flex; align-items: center; padding-left: 52px; }
  .variety-band__name { font-family: "Bodoni Moda", Georgia, serif; font-size: 28px; color: var(--band-text); }

  .window-art { position: absolute; left: 80px; top: 590px; width: 360px; height: 300px; background: linear-gradient(135deg, var(--pasta-light), var(--pasta-dark)); }
</style>
</head>
<body>
  <main class="dieline">
    <section class="panel panel--side" aria-label="Seitenteil">
      <p class="cook-time">KOCHZEIT<br>3 MINUTEN</p>
      <div class="cook-icon" role="img" aria-label="Piktogramm Kochtopf mit Dampf"></div>
      <div class="side-band"></div>
      <p class="side-copy side-copy--intro">Feine Pasta aus Buchweizenmehl und Hartweizengrieß, schonend getrocknet.</p>
      <p class="side-copy side-copy--info">Zutaten: Buchweizenmehl, Hartweizengrieß, Wasser. Kann Spuren von Soja enthalten. Trocken lagern und vor Licht schützen.</p>
      <p class="side-copy side-copy--prep">Zubereitung: Pasta in reichlich kochendes Salzwasser geben und drei Minuten garen. Abgießen, nach Belieben mit Öl, Kräutern oder Sauce servieren. Mit liebevoller Handarbeit in kleinen Mengen hergestellt, für besten Geschmack und Biss.</p>
      <div class="vegan-badge" role="img" aria-label="Siegel vegan"></div>
      <p class="net-weight">250g ℮</p>
    </section>

    <section class="panel panel--front" aria-label="Vorderseite">
      <div class="brand">
        <span class="brand__mark"></span>
        <span class="brand__name">VELMORIA</span>
      </div>
      <h1 class="product-title">
        <span class="product-title__sub">BUCHWEIZEN</span>
        <span class="product-title__main">PASTA</span>
      </h1>
      <span class="product-title__script">Buckwheat</span>
      <div class="variety-band"><span class="variety-band__name">fusilli</span></div>
      <div class="window-art" role="img" aria-label="Sichtfenster mit Blick auf Buchweizen-Fusilli und Illustration von Spiralnudeln mit Buchweizenkörnern"></div>
    </section>
  </main>
</body>
</html>
```